wine label for ultra premium vineyard in Bendigo, Central Otago, New Zealand

"WREN" is our new wine brand, with grapes grown in our spectacular "ter Hoeven" vineyard. The small, elevated vineyard overlooks a river valley and snowy mountains. We would like a highly elegant label for our 2018 pinot noir wine, which highlights the quality of wine and our very special vineyard location. "WREN" has to be prominent, with secondary emphasis on "ter Hoeven vineyard" and "Bendigo, Central Otago". A stylized WREN logo (bird) could be a useful design device instead of the commonly seen illustrated mountain landscape (which is quite common for our local wines). Label size 90 high, 110 wide. Please use a pinot noir / burgundy bottle. See here for vineyard pics, and also below pics for other local wine labels and pics for inspiration / styles. https://www.instagram.com/jan.ter.hoeven/

Target Market(s)

average bottle price for this premium red pinot noir would be aroundUS$40. target market are generally urban professionals aged 25 and older with a high degree of interest in pinot noir wine, and who are familiar with New Zealand pinot noir (ie. already know several brands).

Colors
ed252d

Requirements
Must have
• distinctive label, sophisticated look
Nice to have
• classy white paper stock
Should not have
• label must not get too busy... less but high quality and distinctive is more....

```html
<!DOCTYPE html>
<html lang="en">
<head>
<meta charset="utf-8">
<title>WREN — Ter Hoeven Vineyard Pinot Noir 2018 Label</title>
<link rel="stylesheet" href="https://fonts.googleapis.com/css2?family=Bodoni+Moda:opsz,wght@6..96,400&family=Tinos&display=swap">
<style>
  :root {
    --stage: #121012;
    --label-red: #ed252d;
    --label-red-deep: #f3343c;
    --label-glow: #f87078;
    --ink: #ffffff;
  }
  html, body {
    margin: 0;
    width: 1156px;
    height: 1200px;
    overflow: hidden;
    background: var(--stage);
  }
  .canvas {
    position: relative;
    width: 1156px;
    height: 1200px;
  }
  .label {
    position: absolute;
    left: 78px;
    top: 191px;
    width: 1000px;
    height: 817px;
    background:
      radial-gradient(ellipse 70% 60% at 22% 18%, var(--label-glow) 0%, rgba(248,112,120,0) 70%),
      linear-gradient(160deg, var(--label-red-deep) 0%, var(--label-red) 100%);
    color: var(--ink);
    font-family: "Tinos", "Times New Roman", serif;
  }
  .label__frame {
    position: absolute;
    inset: 10px;
    border: 3px solid var(--ink);
  }
  .label__brand {
    position: absolute;
    left: 0;
    right: 0;
    top: 30px;
    margin: 0;
    text-align: center;
    font-family: "Bodoni Moda", "Didot", serif;
    font-weight: 400;
    font-size: 206px;
    line-height: 1;
    letter-spacing: -4px;
  }
  .label__bird {
    position: absolute;
    left: 151px;
    top: 328px;
    width: 259px;
    height: 263px;
    border-radius: 50% 50% 40% 40%;
    background: radial-gradient(ellipse at 55% 45%, rgba(255,255,255,0.35) 0%, rgba(255,255,255,0.1) 60%, rgba(255,255,255,0) 75%);
  }
  .label__line {
    position: absolute;
    margin: 0;
    line-height: 1;
    white-space: nowrap;
    font-weight: 400;
  }
  .label__vineyard {
    left: 412px;
    top: 429px;
    font-size: 39px;
  }
  .label__region {
    left: 480px;
    top: 521px;
    font-size: 30px;
  }
  .label__vintage {
    left: 0;
    right: 0;
    top: 684px;
    padding-left: 0;
    text-align: center;
    font-size: 30px;
  }
  .label__varietal {
    left: 0;
    right: 0;
    top: 767px;
    padding-left: 6px;
    text-align: center;
    font-size: 32px;
  }
</style>
</head>
<body>
  <main class="canvas">
    <section class="label" aria-label="WREN Pinot Noir wine label">
      <div class="label__frame"></div>
      <h1 class="label__brand">WREN</h1>
      <div class="label__bird" role="img" aria-label="Engraved white illustration of a wren perched on a branch"></div>
      <p class="label__line label__vineyard">TER HOEVEN VINEYARD</p>
      <p class="label__line label__region">BENDIGO, CENTRAL OTAGO</p>
      <p class="label__line label__vintage">-2018-</p>
      <p class="label__line label__varietal">PINOT NOIR</p>
    </section>
  </main>
</body>
</html>
```